Every Shelf Set Neatly or ESN Organized needs a business card design. ESN Organized is a professi

We need a business card design that is clean, sharp and conveys a sense of organization. I already have a logo.

Target Market(s)

Families (specifically mothers), small business owners, parents, seniors

Industry/Entity Type

Business

Contact Information for Business Card

My website is www.esnorganized-example.com and my Facebook page is http://www.sociallink-example.com/everyshelfsetneatly. The phone number is 418-552-7094 and I want to be listed as Lorna M. Pelham, Owner

Requirements
Must have
• My logo.

```html
<!DOCTYPE html>
<html lang="en">
<head>
<meta charset="utf-8">
<title>ESN Organized – Business Card</title>
<link rel="stylesheet" href="https://fonts.googleapis.com/css2?family=Lato:wght@400;700&display=swap">
<style>
  :root {
    --backdrop: #2b2b2b;
    --card: #f4f4f4;
    --ink: #1c1c1c;
    --muted: #3a3a3a;
    --brand-blue: #1f74c9;
    --band-blue: #1b63b0;
    --band-black: #1e1e1e;
    --rule: #8a8a8a;
  }
  html, body {
    margin: 0;
    width: 1200px;
    height: 873px;
    overflow: hidden;
    background: var(--backdrop);
  }
  .business-card {
    position: absolute;
    left: 150px;
    top: 180px;
    width: 900px;
    height: 514px;
    background: var(--card);
    border-radius: 4px;
    overflow: hidden;
    font-family: "Lato", sans-serif;
    color: var(--ink);
  }
  .brand {
    position: absolute;
    top: 100px;
    left: 0;
    width: 100%;
    display: flex;
    justify-content: center;
    align-items: center;
    gap: 18px;
  }
  .brand-mark {
    width: 22px;
    height: 22px;
    background: var(--brand-blue);
  }
  .brand-name {
    font-family: "Lato", sans-serif;
    font-weight: 400;
    font-size: 48px;
    letter-spacing: 0;
    color: var(--ink);
  }
  .holder {
    position: absolute;
    top: 296px;
    left: 70px;
    width: 260px;
    text-align: right;
  }
  .holder-name {
    font-weight: 700;
    font-size: 30px;
    color: var(--brand-blue);
  }
  .holder-title {
    font-size: 23px;
    color: var(--muted);
    margin-top: 2px;
  }
  .divider {
    position: absolute;
    left: 362px;
    top: 258px;
    width: 2px;
    height: 128px;
    background: var(--rule);
  }
  .contact {
    position: absolute;
    left: 390px;
    top: 268px;
    list-style: none;
    margin: 0;
    padding: 0;
    font-size: 22px;
    color: var(--muted);
  }
  .contact li {
    display: flex;
    align-items: center;
    gap: 12px;
    height: 44px;
    white-space: nowrap;
  }
  .contact-icon {
    width: 28px;
    height: 28px;
    flex: none;
  }
  .card-bands {
    position: absolute;
    left: 0;
    bottom: 0;
    width: 900px;
    height: 140px;
  }
  .band-black { fill: var(--band-black); }
  .band-blue { fill: var(--band-blue); }
</style>
</head>
<body>
  <section class="business-card">
    <div class="brand">
      <span class="brand-mark"></span>
      <span class="brand-name">ESN Organized</span>
    </div>

    <div class="holder">
      <div class="holder-name">Lorna M. Pelham</div>
      <div class="holder-title">Owner</div>
    </div>

    <div class="divider"></div>

    <ul class="contact">
      <li>
        <svg class="contact-icon" viewBox="0 0 30 30" aria-hidden="true">
          <circle cx="15" cy="15" r="15" fill="var(--brand-blue)"/>
          <path d="M8 12 Q15 6 22 12 L20 14 L18 12 L12 12 L10 14 Z" fill="#fff"/>
          <rect x="10" y="15" width="10" height="7" rx="1.5" fill="#fff"/>
          <circle cx="15" cy="18.5" r="2" fill="var(--brand-blue)"/>
        </svg>
        <span>418-552-7094</span>
      </li>
      <li>
        <svg class="contact-icon" viewBox="0 0 30 30" aria-hidden="true">
          <circle cx="15" cy="15" r="15" fill="var(--brand-blue)"/>
        </svg>
        <span>sociallink-example.com/everyshelfsetneatly</span>
      </li>
    </ul>

    <svg class="card-bands" viewBox="0 0 900 140" aria-hidden="true">
      <path class="band-black" d="M0 112 L520 52 Q535 50 528 62 L512 86 L0 140 Z"/>
      <path class="band-blue" d="M540 76 Q556 48 600 44 L900 10 L900 34 L548 82 Z"/>
    </svg>
  </section>
</body>
</html>
```